Brightmoor Talent company

We require a website for job recruitment company called "Brightmoor Talent"
Our company is specialising in recruitment of skilled labour from Sri Lanka into Australian market.
We would like to include a job advertising plugin where jobs can be listed and applied for .
COPYWRITING MUST BE INCLUDED !

Industry/Entity Type

Recruitment

Coding

Coded - Design and coding required

Number of Pages Required

5+ page

Colors

Designer to choose colors to be used in the design.

```html
<!DOCTYPE html>
<html lang="en">
<head>
<meta charset="utf-8">
<title>Brightmoor Talent</title>
<link href="https://fonts.googleapis.com/css2?family=Merriweather:wght@700;900&family=Roboto:wght@400;500;700&display=swap" rel="stylesheet">
<style>
:root{
  --blue:#0b4ea2;
  --blue-dark:#0a3c80;
  --navy:#102a52;
  --ink:#2b2f36;
  --muted:#7a7f88;
  --line:#d9dde3;
  --tint:#eef2f7;
  --charcoal:#4b4b4d;
  --footer:#565658;
  --footer-deep:#3f3f41;
  --white:#ffffff;
}
*{box-sizing:border-box;margin:0;padding:0}
html,body{width:1200px;height:3776px;overflow:hidden}
body{position:relative;background:var(--white);font-family:'Roboto',Arial,sans-serif;color:var(--ink)}
.abs{position:absolute}
.serif{font-family:'Merriweather',Georgia,serif}

/* header */
.brand{left:24px;top:34px;font-family:'Merriweather',Georgia,serif;font-weight:900;font-size:30px;color:var(--navy);line-height:1.1;width:240px}
.topbar{top:0;left:560px;height:40px;display:flex;align-items:center;gap:28px;font-size:13px;color:var(--ink)}
.topbar span{display:flex;align-items:center;gap:8px}
.quote-btn{right:8px;top:0;width:264px;height:40px;background:var(--navy);color:#fff;font-size:13px;font-weight:700;display:flex;align-items:center;justify-content:center;letter-spacing:.5px}
.nav{top:76px;left:432px;display:flex;gap:34px;font-size:14px;font-weight:500;color:var(--ink)}
.nav .active{color:var(--blue);border-bottom:2px solid var(--blue);padding-bottom:6px}
.socials{top:70px;left:936px;display:flex;gap:12px}
.socials i{display:block;width:32px;height:32px;border-radius:50%;background:#e6e8ec}
.socials i.first{background:var(--blue)}

/* hero */
.hero{top:144px;left:0;width:1200px;height:600px;background:linear-gradient(90deg,#3b4654 0%,#8a949f 45%,#c9ced4 70%,#9aa3ad 100%)}
.hero-shade{top:144px;left:0;width:620px;height:600px;background:linear-gradient(90deg,rgba(14,24,40,.55),rgba(14,24,40,0))}
.hero-title{left:112px;top:328px;font-size:40px;font-weight:900;color:#fff;letter-spacing:1px;line-height:1.2}
.hero-title b{color:#9cc4ff;font-weight:900}
.hero-copy{left:112px;top:386px;width:420px;font-size:16px;line-height:1.45;color:#fff}
.hero-btn{left:112px;top:468px;width:148px;height:44px;background:var(--blue);color:#fff;font-size:13px;font-weight:700;display:flex;align-items:center;justify-content:center}

/* about */
.about-block{left:92px;top:1128px;width:112px;height:124px;background:var(--blue)}
.about-img{left:120px;top:872px;width:480px;height:348px;background:linear-gradient(135deg,#e9ecef,#b8bfc7 60%,#7e8893)}
.section-title{font-family:'Merriweather',Georgia,serif;font-weight:900;color:var(--ink);font-size:44px;letter-spacing:1px}
.section-title b{color:var(--blue)}
.about-title{left:648px;top:896px}
.about-copy{left:648px;top:976px;width:512px;font-size:14px;line-height:1.75;color:var(--muted)}
.outline-btn{left:648px;top:1164px;width:136px;height:48px;border:2px solid var(--ink);font-size:13px;font-weight:700;display:flex;align-items:center;justify-content:center}

/* services */
.services{top:1380px;left:0;width:1200px;height:640px;background:var(--tint)}
.services-title{top:1444px;left:0;width:1200px;text-align:center}
.card{top:1532px;width:296px;height:420px;background:#fff;box-shadow:0 6px 22px rgba(16,42,82,.12)}
.card .photo{height:228px}
.card .icon{position:absolute;left:116px;top:196px;width:64px;height:64px;border-radius:50%;background:var(--blue);border:4px solid #fff;display:flex;align-items:center;justify-content:center}
.card h3{position:absolute;top:284px;width:100%;text-align:center;font-size:16px;font-weight:700;letter-spacing:.5px}
.card p{position:absolute;top:316px;left:28px;right:28px;text-align:center;font-size:13px;line-height:1.6;color:var(--muted)}

/* advertise */
.advert{top:2032px;left:0;width:1200px;height:688px;background:linear-gradient(120deg,var(--blue-dark),var(--blue) 60%,#0d57b4)}
.advert-title{top:2100px;left:0;width:1200px;text-align:center;color:#fff;font-size:34px}
.advert-photo{left:196px;top:2236px;width:328px;height:328px;border-radius:50%;background:radial-gradient(circle at 50% 45%,#f3f4f6,#d6dae0 70%);border:10px solid #fff}
.step{left:620px;display:flex;align-items:center;gap:24px;color:#fff;font-size:20px;font-weight:500;line-height:1.4}
.step i{flex:none;width:60px;height:60px;border-radius:50%;background:#fff;display:flex;align-items:center;justify-content:center}

/* contact */
.contact-dark{left:112px;top:2820px;width:328px;height:420px;background:var(--charcoal)}
.contact-kicker{left:112px;top:2912px;width:300px;text-align:right;color:#fff;font-size:15px;font-weight:700;letter-spacing:1px}
.contact-big{left:112px;top:2948px;width:300px;text-align:right;color:#fff;font-family:'Merriweather',Georgia,serif;font-weight:900;font-size:34px;line-height:1.3}
.frame{left:740px;top:2836px;width:356px;height:420px;border:3px solid var(--blue)}
.form{left:460px;top:2860px;width:628px;height:452px;background:#fff;box-shadow:0 8px 30px rgba(0,0,0,.14)}
.form-title{left:516px;top:2898px;font-family:'Merriweather',Georgia,serif;font-size:24px;font-weight:700;color:var(--ink)}
.form-title b{color:var(--blue)}
.field{width:236px;border-bottom:1px solid var(--line);padding-bottom:8px}
.field label{display:block;font-size:14px;font-weight:500;color:var(--ink);margin-bottom:10px}
.field span{font-size:12px;color:#a3a8b0}
.field.wide{width:508px}
.send{left:962px;top:3212px;width:60px;height:60px;border-radius:50%;background:var(--blue);display:flex;align-items:center;justify-content:center}

/* footer */
.footer{top:3400px;left:0;width:1200px;height:320px;background:var(--footer)}
.footer-bar{top:3720px;left:0;width:1200px;height:56px;background:var(--footer-deep);color:#ddd;font-size:12px;display:flex;align-items:center;justify-content:center}
.footer-brand{left:72px;top:3536px;width:260px;font-family:'Merriweather',Georgia,serif;font-weight:900;font-size:30px;color:#fff;line-height:1.15}
.f-head{font-size:14px;font-weight:700;color:#fff;letter-spacing:.5px}
.f-list{list-style:none;color:#e3e3e3;font-size:12px;line-height:2.2}
.f-list li::before{content:"";display:inline-block;width:6px;height:6px;border-radius:50%;background:#9cc4ff;margin-right:10px;vertical-align:middle}
.f-info{color:#e3e3e3;font-size:12px;line-height:1.55}
.f-info b{display:block;color:#fff;font-size:12px;margin-top:12px}
.news{left:800px;top:3446px;display:flex}
.news span{width:200px;height:40px;background:#fff;font-size:12px;color:#888;display:flex;align-items:center;padding-left:14px}
.news b{width:92px;height:40px;background:var(--blue);color:#fff;font-size:12px;display:flex;align-items:center;justify-content:center}
.f-socials{left:800px;top:3512px;display:flex;gap:10px}
.f-socials i{width:28px;height:28px;border-radius:50%;background:var(--blue)}
</style>
</head>
<body>

<!-- header -->
<div class="abs brand">Brightmoor Talent</div>
<div class="abs topbar">
  <span><svg width="14" height="14" viewBox="0 0 24 24"><path fill="#0b4ea2" d="M6.6 10.8a15 15 0 006.6 6.6l2.2-2.2c.3-.3.7-.4 1-.2 1.1.4 2.3.6 3.6.6.6 0 1 .4 1 1V20c0 .6-.4 1-1 1C10.6 21 3 13.4 3 4c0-.6.4-1 1-1h3.5c.6 0 1 .4 1 1 0 1.3.2 2.5.6 3.6.1.3 0 .7-.2 1z"/></svg>+61 (02) 5550 1842</span>
  <span><svg width="15" height="12" viewBox="0 0 24 18"><rect x="1" y="1" width="22" height="16" rx="2" fill="none" stroke="#0b4ea2" stroke-width="2"/><path d="M1 2l11 8 11-8" fill="none" stroke="#0b4ea2" stroke-width="2"/></svg>info@brightmoortalent.com</span>
</div>
<div class="abs quote-btn">REQUEST A QUOTE</div>
<nav class="abs nav">
  <span class="active">HOME</span><span>ABOUT US</span><span>SERVICES</span><span>CAREER</span><span>CONTACT US</span>
</nav>
<div class="abs socials"><i class="first"></i><i></i><i></i><i></i></div>

<!-- hero -->
<div class="abs hero" role="img" aria-label="Business people meeting in a bright modern office lobby"></div>
<div class="abs hero-shade"></div>
<h1 class="abs hero-title serif">BRIGHTMOOR <b>TALENT</b></h1>
<p class="abs hero-copy">Connecting skilled Sri Lankan workers with trusted employers across Australia.</p>
<div class="abs hero-btn">GET STARTED</div>

<!-- about -->
<div class="abs about-block"></div>
<div class="abs about-img" role="img" aria-label="Recruiter working at a computer in an office"></div>
<h2 class="abs section-title about-title">ABOUT <b>US</b></h2>
<p class="abs about-copy">Brightmoor Talent specialises in recruiting skilled labour from Sri Lanka for the Australian market. We source, screen and prepare tradespeople, technicians and professionals, then match them with employers who need reliable staff. Our team handles advertising, applications, interviews and paperwork, so every placement runs smoothly from first contact to the first day on site.</p>
<div class="abs outline-btn">READ MORE</div>

<!-- services -->
<div class="abs services"></div>
<h2 class="abs section-title services-title">OUR <b>SERVICES</b></h2>

<div class="abs card" style="left:112px">
  <div class="photo" role="img" aria-label="Skilled worker welding in a workshop" style="background:linear-gradient(135deg,#3a2a1c,#b8742e 55%,#e8b060)"></div>
  <div class="icon"><svg width="28" height="28" viewBox="0 0 24 24"><path fill="#fff" d="M22 19l-9-9c.9-2.3.4-5-1.5-6.9A6 6 0 005 2.7L9 6.7 6.7 9 2.6 5a6 6 0 001.4 6.5c1.9 1.9 4.6 2.4 6.9 1.5l9 9z"/></svg></div>
  <h3>SKILLED LABOUR</h3>
  <p>Qualified tradespeople ready to fill roles across Australian industries.</p>
</div>
<div class="abs card" style="left:452px">
  <div class="photo" role="img" aria-label="Professionals working on a building site" style="background:linear-gradient(135deg,#6d4a2c,#c08a4f 55%,#e2c39a)"></div>
  <div class="icon"><svg width="28" height="28" viewBox="0 0 24 24"><rect x="3" y="7" width="18" height="13" rx="2" fill="#fff"/><path d="M9 7V5h6v2" fill="none" stroke="#fff" stroke-width="2"/></svg></div>
  <h3>PROFESSIONALS</h3>
  <p>Engineers, nurses and specialists screened for skills and experience.</p>
</div>
<div class="abs card" style="left:792px">
  <div class="photo" role="img" aria-label="Engineers in hard hats reviewing plans on site" style="background:linear-gradient(135deg,#8b7a66,#c9b9a2 55%,#7d8a6c)"></div>
  <div class="icon"><svg width="28" height="28" viewBox="0 0 24 24"><path fill="#fff" d="M12 2l3 6 6.5 1-4.7 4.6 1.1 6.4L12 17l-5.9 3 1.1-6.4L2.5 9 9 8z"/></svg></div>
  <h3>EXPERIENCE</h3>
  <p>Years of recruitment know-how behind every match we make.</p>
</div>

<!-- advertise -->
<div class="abs advert"></div>
<h2 class="abs serif advert-title">WE ADVERTISE FOR A JOB IN</h2>
<svg class="abs" style="left:0;top:2032px" width="1200" height="688" viewBox="0 0 1200 688">
  <g fill="none" stroke="rgba(255,255,255,.55)" stroke-width="2">
    <circle cx="360" cy="368" r="206"/>
    <path d="M520 240 Q580 180 620 176"/>
    <path d="M560 330 Q590 320 620 320"/>
    <path d="M560 420 Q590 456 620 456"/>
    <path d="M520 500 Q580 590 620 592"/>
  </g>
</svg>
<div class="abs advert-photo" role="img" aria-label="Smiling young woman sitting with a laptop"></div>
<div class="abs step" style="top:2178px"><i><svg width="26" height="26" viewBox="0 0 24 24"><rect x="3" y="4" width="18" height="16" rx="1" fill="none" stroke="#0b4ea2" stroke-width="2"/><path d="M7 9h10M7 13h10M7 17h6" stroke="#0b4ea2" stroke-width="2"/></svg></i><span>Sri Lankan Newspapers and<br>social media</span></div>
<div class="abs step" style="top:2322px"><i><svg width="26" height="26" viewBox="0 0 24 24"><path d="M6 3h9l4 4v14H6z" fill="none" stroke="#0b4ea2" stroke-width="2"/><path d="M9 12h7M9 16h7" stroke="#0b4ea2" stroke-width="2"/></svg></i><span>Collecting applications</span></div>
<div class="abs step" style="top:2458px"><i><svg width="26" height="26" viewBox="0 0 24 24"><circle cx="10" cy="10" r="6" fill="none" stroke="#0b4ea2" stroke-width="2"/><path d="M15 15l6 6" stroke="#0b4ea2" stroke-width="2"/></svg></i><span>Reviewing the suitable candidates</span></div>
<div class="abs step" style="top:2594px"><i><svg width="26" height="26" viewBox="0 0 24 24"><path d="M4 12l5 5L20 6" fill="none" stroke="#0b4ea2" stroke-width="2.5"/></svg></i><span>Shortlist candidates and organise<br>job interviews</span></div>

<!-- contact -->
<div class="abs contact-dark"></div>
<div class="abs contact-kicker">CONTACT US</div>
<div class="abs contact-big">LET'S DO<br>GOOD<br>TOGETHER!</div>
<div class="abs frame"></div>
<div class="abs form"></div>
<h2 class="abs form-title">SEND US A <b>MESSAGE</b></h2>
<div class="abs field" style="left:516px;top:2966px"><label>First Name</label><span>John</span></div>
<div class="abs field" style="left:788px;top:2966px"><label>Last Name</label><span>Smith</span></div>
<div class="abs field" style="left:516px;top:3050px"><label>Email Address</label><span>name@email.com</span></div>
<div class="abs field" style="left:788px;top:3050px"><label>Phone</label><span>+61 (02) 5550 0000</span></div>
<div class="abs field wide" style="left:516px;top:3134px"><label>Message</label><span>Tell us about the role you need to fill...</span></div>
<div class="abs send"><svg width="24" height="24" viewBox="0 0 24 24"><path fill="#fff" d="M2 21l21-9L2 3v7l15 2-15 2z"/></svg></div>

<!-- footer -->
<div class="abs footer"></div>
<div class="abs footer-brand">Brightmoor Talent</div>
<div class="abs" style="left:392px;top:3448px"><div class="f-head">QUICK LINKS</div>
  <ul class="f-list" style="margin-top:10px"><li>Home</li><li>About Us</li><li>Services</li><li>Careers</li><li>Contact Us</li></ul></div>
<div class="abs" style="left:576px;top:3448px;width:180px"><div class="f-head">CONTACT INFO</div>
  <div class="f-info"><b>ADDRESS:</b>18 Harbour Lane, Colombo,<br>Sri Lanka<b>PHONE:</b>+61 (02) 5550 1842<b>EMAIL:</b>info@brightmoortalent.com</div></div>
<div class="abs f-head" style="left:800px;top:3418px">NEWSLETTER SIGNUP</div>
<div class="abs news"><span>Email Address</span><b>SIGN UP</b></div>
<div class="abs f-socials"><i></i><i></i><i></i><i></i></div>
<div class="abs footer-bar">© 2020 BRIGHTMOOR TALENT &nbsp;|&nbsp; All Rights Reserved</div>

</body>
</html>
```